Company Website Re-design for Software development consultancy

We would like our company website to be redesigned using our existing marketing collateral and website content as a guide

current site : www.brightkestrel.com.au

For the different pages types and content please base on the following site : https://www.quorvalabs.net/

We want a coded site - but will replace the content ourselves within the sections you provide to customise to our needs.

Target Market(s)

Medium to Large corporates needing software design and development services

Industry/Entity Type

Information Technology

Coding

Coded - Design and coding required

Number of Pages Required

5+ page

Font styles to use
Sans Serif

Colors
ec1f27
ffffff
000000

Requirements
Must have
• Align to colour scheme of existing collateral
• Include pages for the key areas of our busines - see : https://www.quorvalabs.net/
Nice to have
• image rotators - make the site interesting to the business visitor

```html
<!DOCTYPE html>
<html lang="en">
<head>
<meta charset="utf-8">
<title>Bright Kestrel — Product &amp; Services</title>
<link rel="stylesheet" href="https://fonts.googleapis.com/css2?family=Poppins:wght@500;600&family=Lato:wght@400&family=Roboto:wght@400;500&display=swap">
<style>
:root{
  --brand-red:#ec1f27;
  --deep-red:#7a0008;
  --ink:#000000;
  --paper:#ffffff;
  --body-grey:#444444;
  --footer-bg:#efefef;
  --footer-text:#555555;
  --icon-grey:#d4d4d4;
}
*{margin:0;padding:0;box-sizing:border-box}
html,body{width:767px;height:1200px;overflow:hidden;background:var(--paper)}
.page{position:relative;width:767px;height:1200px;overflow:hidden;font-family:'Lato',sans-serif}
.hero{position:absolute;left:0;top:0;width:767px;height:280px;
  background:linear-gradient(100deg,#1c2230 0%,#2a3446 45%,#3b5676 75%,#22304a 100%)}
.hero-shade{position:absolute;inset:0;background:rgba(0,0,0,.35)}
.brand{position:absolute;left:117px;top:20px;font-family:'Poppins',sans-serif;font-weight:600;font-size:19px;color:var(--paper);letter-spacing:.5px;display:flex;align-items:center;gap:7px}
.brand-dot{width:9px;height:9px;border-radius:50%;background:var(--brand-red)}
.main-nav{position:absolute;top:26px;left:308px;display:flex;font-family:'Roboto',sans-serif;font-size:10.5px;font-weight:500;color:var(--paper)}
.main-nav a{color:inherit;text-decoration:none;position:absolute;white-space:nowrap}
.hero-title{position:absolute;top:152px;width:100%;text-align:center;font-family:'Poppins',sans-serif;font-weight:600;font-size:30px;color:var(--paper)}
.section-title{position:absolute;top:314px;width:100%;text-align:center;font-family:'Poppins',sans-serif;font-weight:500;font-size:17px;color:var(--ink)}
.service{position:absolute;width:330px}
.service h2{font-family:'Poppins',sans-serif;font-weight:500;font-size:19px;line-height:24px;text-transform:uppercase}
.service .rule{width:35px;height:2px;margin:7px 0 19px}
.service p{font-size:10px;line-height:16.4px;color:var(--body-grey)}
.service--light h2{color:var(--brand-red)}
.service--light .rule{background:var(--ink)}
.service--dark h2{color:var(--ink)}
.service--dark .rule{background:var(--ink)}
.service--on-red h2,.service--on-red p{color:var(--paper)}
.service--on-red .rule{background:var(--paper)}
.band{position:absolute;left:0;top:560px}
.service-icon{position:absolute;border-radius:10px}
.site-footer{position:absolute;left:0;top:1148px;width:767px;height:52px;background:var(--footer-bg)}
.copyright{position:absolute;left:237px;top:19px;font-family:'Roboto',sans-serif;font-size:10px;color:var(--footer-text)}
.social{position:absolute;top:19px;left:541px;display:flex;gap:17px}
.social span{width:13px;height:13px;border-radius:50%;background:#6a6a6a;display:block}
</style>
</head>
<body>
<div class="page">
  <header class="hero" role="img" aria-label="Photo of a development team reviewing app screens on a monitor">
    <div class="hero-shade"></div>
    <div class="brand"><span>BRIGHT KESTREL</span><span class="brand-dot"></span></div>
    <nav class="main-nav">
      <a href="#" style="left:0">ABOUT US</a>
      <a href="#" style="left:69px">PRODUCTS AND SERVICES</a>
      <a href="#" style="left:212px">BLOG ARTICLE</a>
      <a href="#" style="left:302px">CONTACT</a>
    </nav>
    <h1 class="hero-title">PRODUCT &amp; SERVICES</h1>
  </header>

  <h2 class="section-title">OUR PRODUCT &amp; SERVICES</h2>

  <article class="service service--light" style="left:123px;top:378px">
    <h2>Software<br>Development</h2>
    <div class="rule"></div>
    <p>Integer congue augue et malesuada iaculis ipsum dui aliquet felis at cursus magna nisl nec elit Praesent elementum elit at tellus nec ultricies sit amet porttitor mattis enim In massa libero interdum nec interdum vel blandit sed nulla In ullamcorper est eget tempor cursus neque mi con-sectetuer mi a ultricies massa est sed nisl Class aptent</p>
  </article>
  <div class="service-icon" style="left:490px;top:375px;width:147px;height:145px;background:var(--icon-grey)" role="img" aria-label="Line icon of a laptop showing code"></div>

  <svg class="band" width="767" height="340" viewBox="0 560 767 340" aria-hidden="true">
    <defs>
      <linearGradient id="bandFill" x1="0" y1="0" x2="1" y2="1">
        <stop offset="0" stop-color="#6e0006"/>
        <stop offset=".55" stop-color="#b00014"/>
        <stop offset="1" stop-color="#e8102a"/>
      </linearGradient>
    </defs>
    <polygon points="0,574 767,569 767,600 510,592" fill="#6e0006"/>
    <polygon points="0,574 510,592 767,600 767,895 210,875 0,890" fill="url(#bandFill)"/>
    <polygon points="510,592 767,585 767,600" fill="var(--brand-red)"/>
    <polygon points="0,866 210,875 0,890" fill="#6e0006"/>
  </svg>

  <div class="service-icon" style="left:180px;top:625px;width:109px;height:185px;background:rgba(255,255,255,.25)" role="img" aria-label="Line icon of a smartphone with app layout"></div>
  <article class="service service--on-red" style="left:357px;top:648px">
    <h2>Mobile App<br>Development</h2>
    <div class="rule"></div>
    <p>Integer congue augue et malesuada iaculis ipsum dui aliquet felis at cursus magna nisl nec elit Praesent elementum elit at tellus nec ultricies sit amet porttitor mattis enim In massa libero interdum nec interdum vel blandit sed nulla In ullamcorper est eget tempor cursus neque mi con-sectetuer mi a ultricies massa est sed nisl Class aptent</p>
  </article>

  <article class="service service--dark" style="left:123px;top:940px">
    <h2>IT Consulting<br>Services</h2>
    <div class="rule"></div>
    <p>Integer congue augue et malesuada iaculis ipsum dui aliquet felis at cursus magna nisl nec elit Praesent elementum elit at tellus nec ultricies sit amet porttitor mattis enim In massa libero interdum nec interdum vel blandit sed nulla In ullamcorper est eget tempor cursus neque mi con-sectetuer mi a ultricies massa est sed nisl Class aptent</p>
  </article>
  <div class="service-icon" style="left:485px;top:925px;width:147px;height:147px;background:var(--icon-grey)" role="img" aria-label="Line icon of a head with a gear and circuit lines"></div>

  <footer class="site-footer">
    <p class="copyright">© 2018 Company Name&nbsp; All right reserved&nbsp; Term of Use</p>
    <div class="social" aria-label="Social links"><span></span><span></span><span></span><span></span></div>
  </footer>
</div>
</body>
</html>
```